Wordpress Theme for Medical Clinics

** Please view updated Sitemap2.pdf doc to clarify some confusion ***

This is a multiuser WordPress subscription site for medical clinics. Please see attachment for sitemap. Please do not include extra content like social media icons, search bars, or images. If you have questions, please ask for clarification.
The site contains the following pages and sub-pages:

1. Home
2. Our Clinic
2a. Our Clinic > Mission
2b. Our Clinic > Services
2c. Our Clinic > Clinic Policies
2d. Our Clinic > Schedules
3. Our Staff
3a. Our Staff > [Staff member page]
4. Resources
4a. Resources > Patient Health (index)
4b. Resources > Patient Health (index) > [post]
4c. Resources > Links
4d. Resources > Forms
5. Alerts
5a. Alerts > [Alert Page]
6. Contact Us

Includes the Following Pages, Subpages, and Content
1. Home
a. About Us
b. Our Staff
c. Bulletins
d. Accepting New Patients (shown as an alert widget)
e. Links
i. Physician Toolbox
ii. Book an Appointment
f. Clinic Policies
i. Show first 3 policies (e.g. Late Arrivals, Missed Appointments, Fees)
ii. Link to Clinic Policies page
g. Primary widget (displayed on all pages)
i. Hours of operation
ii. Contact Info
1. Tel
2. Fax
3. Email
4. Address
5. Get directions (link to Google Maps)
2. Our Clinic
a. Main Page
i. Clinic Name
ii. Overview
iii. Languages Spoken
iv. Secondary Navigation
1. Mission
2. Services
3. Clinic Policies
4. Schedules (see attachment)
b. Our Clinic > Mission
c. Our Clinic > Services
i. For each service include service TITLE and DESCRIPTION
d. Our Clinic > Clinic Policies
i. For each policy include policy TITLE and DESCRIPTION
ii. Include the following policies in mockup
1. Late arrivals
2. Missed appointments
3. Fees for missed appointments
4. Referrals and follow-ups
5. Services not covered by RDA
6. Information for LTF patients
7. Medical Legal Reports
e. Our Clinic > Schedules
3. Our Staff
a. Main Page
i. Display a list of staff members. Include NAME and DESIGNATION
b. Our Staff > [Staff Name]
i. Include NAME, PICTURE, DESIGNATION, and BIO
4. Resources
a. Resources > Patient Health
i. Main Page
1. Posts (ordered by date)
a. Title
b. Summary
2. Side Navigation
a. Post Categories
ii. Patient Health > [post title]
1. Title
2. Post Category
3. Date
4. Author
5. Summary
6. Body
b. Resources > Links
1. Secondary Navigation - Categories
a. Sample Categories:
i. Local Services
ii. RDA and Drug Coverage
iii. Mental Health Resources
2. Category page
a. Include the following links in the 'Local Services' category
i. Hypertension clinics
ii. Home Care services
iii. Vaccine Clinics
c. Resources > Forms
i. Display a table with form TITLE and CATEGORY
ii. Side Navigation
1. Form Categories
a. Use the following sample Categories
i. Referrals
ii. Insurance
iii. Intake
iv. Discharge
v. Waivers
5. Alerts
a. Main page
i. List of all Alert posts
1. Include post TITLE as a link to the post
ii. Side Navigation
1. Alerts Archive
a. shown as Month + Number of posts
iii. Alerts > [Alert page]
1. Include TITLE, DATE, AUTHOR, BODY
6. Contact Us
a. Map
b. Hours of operation
c. Address
d. Phone number
e. Fax number
e. Fax number
f. Map
g. Email

Design notes:
- fixed width
- responsive (need designs for mobile, tablet, and desktop)
- simple, dark font, white background
- use Font Awesome icons where needed
- user adds own logo

Target Market(s)

Medical Clinics

Industry/Entity Type

Medical

Number of Pages Required

5+ page

Font styles to use
Serif
Sans Serif

Requirements
Must have
• Please keep designs very simple.
• Examples:
• https://www.quolbin.com/install
• http://www.ventrohax.com/company/about-us
• http://brindlequota.org/
• http://www.trosk.com/
Should not have
• Minimal or no use of shadows and gradients

```html
<!DOCTYPE html>
<html lang="en">
<head>
<meta charset="utf-8">
<title>Orrin Clinics</title>
<link rel="stylesheet" href="https://fonts.googleapis.com/css2?family=Roboto:wght@400;500&family=Signika:wght@400;600&display=swap">
<style>
:root{
  --blue:#1a9ad3;
  --blue-dark:#1285bb;
  --green:#3fae2a;
  --ink:#1d1d1d;
  --text:#333;
  --muted:#8a8a8a;
  --band:#efefef;
  --panel:#e9eff4;
  --footer:#0c0c0c;
  --white:#fff;
}
*{margin:0;padding:0;box-sizing:border-box}
html,body{width:754px;height:1200px;overflow:hidden;background:var(--white)}
body{position:relative;font-family:"Roboto",Arial,sans-serif;color:var(--text)}
.abs{position:absolute}

/* header */
.site-header{position:absolute;left:0;top:0;width:754px;height:66px}
.brand{left:70px;top:21px;display:flex;align-items:center;gap:6px;font-size:16px;letter-spacing:.5px;color:var(--ink)}
.brand-mark{width:18px;height:18px;background:var(--blue)}
.contact-today{left:440px;top:26px;width:97px;text-align:right;font-size:7px;color:#444}
.contact-today strong{display:block;font-weight:400;font-size:10px;color:var(--blue);margin-top:3px}
.btn{position:absolute;display:flex;align-items:center;justify-content:center;gap:3px;color:var(--white);font-size:7px;border-radius:2px}
.btn-login{left:551px;top:23px;width:62px;height:25px;background:var(--green)}
.btn-signup{left:621px;top:23px;width:62px;height:25px;background:var(--blue)}

/* nav */
.main-nav{position:absolute;left:0;top:66px;width:754px;height:35px;background:var(--band)}
.nav-item{position:absolute;top:14px;font-size:7px;color:#333}
.nav-home{left:70px;top:7px;width:42px;height:22px;background:var(--blue);color:var(--white);display:flex;align-items:center;justify-content:center;border-radius:2px}
.nav-active{color:var(--blue)}
.dropdown{position:absolute;left:139px;top:96px;width:114px;height:132px;background:var(--blue);border-radius:2px;z-index:2}
.dropdown ul{padding-top:5px}
.dropdown li{list-style:none;height:20.4px;padding:0 13px;font-size:6.8px;color:var(--white);display:flex;align-items:center;justify-content:space-between}
.dropdown li.current{background:var(--blue-dark)}
.plus{width:7px;height:7px;border-radius:50%;background:var(--white);position:relative}
.plus::before,.plus::after{content:"";position:absolute;background:var(--blue)}
.plus::before{left:1.5px;top:3px;width:4px;height:1px}
.plus::after{left:3px;top:1.5px;width:1px;height:4px}
.submenu{position:absolute;left:256px;top:179px;width:104px;height:56px;background:var(--blue-dark);border-radius:2px;padding-top:8px;z-index:2}
.submenu div{height:20.5px;padding-left:13px;font-size:6.8px;color:var(--white);display:flex;align-items:center}

/* hero */
.hero{position:absolute;left:70px;top:108px;width:613px;height:275px;border:1px solid #ddd;padding:1px}
.hero-panel{width:100%;height:100%;background:var(--panel)}
.hero-caption{position:absolute;left:1px;top:158px;width:350px;height:73px;background:var(--white)}
.hero-dots{position:absolute;left:0;top:0;width:23px;height:73px;background:var(--blue)}
.hero-dots span{position:absolute;left:8px;width:7px;height:7px;border-radius:50%;background:var(--white)}
.hero-dots span.on{background:#222}
.hero-caption h2{position:absolute;left:38px;top:11px;font-weight:400;font-size:15.5px;line-height:26px;color:#333;letter-spacing:.2px;white-space:nowrap}

/* sections */
.section-title{position:absolute;left:0;width:754px;text-align:center;font-family:"Signika",sans-serif;font-weight:400;font-size:17px;letter-spacing:.5px;color:var(--ink)}
.lede{position:absolute;left:70px;width:613px;text-align:center;font-size:6.8px;line-height:16px;color:var(--muted)}
.lede .dark{color:#333}

/* home widgets */
.widget{position:absolute;top:497px;width:141px}
.widget-box{height:81px;border:2px solid #eee;background:var(--white);padding:7px 8px;font-size:6.4px;line-height:11.6px;color:#444}
.widget-box .row{display:flex;justify-content:space-between}
.widget-box .alert{display:inline-block;background:var(--green);color:var(--white);padding:0 5px;border-radius:2px;margin-bottom:3px}
.widget-box a{color:var(--blue)}
.widget h3{margin-top:12px;font-size:7.2px;font-weight:500;color:#333}
.widget p{margin-top:8px;font-size:6.4px;line-height:12.8px;color:var(--muted)}

.band{position:absolute;left:0;width:754px;background:var(--band)}
.btn-blue{position:absolute;background:var(--blue);color:var(--white);font-size:7px;display:flex;align-items:center;justify-content:center;gap:3px;border-radius:2px}

.staff{position:absolute;top:880px;width:190px;text-align:center}
.staff h4{font-weight:500;font-size:9.5px;letter-spacing:.4px;color:var(--blue)}
.staff .role{margin-top:3px;font-size:6.8px;color:#444}
.staff p{margin-top:8px;font-size:6.3px;line-height:13px;color:var(--muted)}

.cta-text{position:absolute;left:80px;top:1030px;width:594px;text-align:center;font-size:9.8px;line-height:16px;color:#222}

/* footer */
.site-footer{position:absolute;left:0;top:1116px;width:754px;height:84px;background:var(--footer);color:#cfcfcf}
.f-contact{position:absolute;top:18px;display:flex;align-items:center;gap:4px;font-size:7px}
.f-rule{position:absolute;left:70px;top:44px;width:613px;height:1px;background:#222}
.f-links{position:absolute;left:70px;top:58px;font-size:6.5px;color:#aaa}
.f-copy{position:absolute;right:70px;top:58px;font-size:6.5px;color:#aaa}
</style>
</head>
<body>

<header class="site-header">
  <div class="abs brand"><span class="brand-mark"></span>ORRIN CLINICS</div>
  <div class="abs contact-today">CONTACT US TODAY!<strong>555-014-2290</strong></div>
  <a class="btn btn-login"><svg width="6" height="7" viewBox="0 0 6 7"><circle cx="3" cy="2" r="1.8" fill="#fff"/><path d="M0 7c0-2.2 1.3-3 3-3s3 .8 3 3z" fill="#fff"/></svg>LOGIN</a>
  <a class="btn btn-signup"><svg width="9" height="7" viewBox="0 0 9 7"><circle cx="4.5" cy="2" r="1.7" fill="#fff"/><circle cx="1.6" cy="2.6" r="1.2" fill="#fff"/><circle cx="7.4" cy="2.6" r="1.2" fill="#fff"/><path d="M2 7c0-2 1-3 2.5-3S7 5 7 7z" fill="#fff"/></svg>SIGNUP</a>
</header>

<nav class="main-nav">
  <a class="nav-item nav-home">HOME</a>
  <a class="nav-item nav-active" style="left:139px">CLINIC</a>
  <a class="nav-item" style="left:200px">OUR STAFF</a>
  <a class="nav-item" style="left:277px">RESOURCES</a>
  <a class="nav-item" style="left:356px">CONTACT US</a>
</nav>

<section class="hero">
  <div class="hero-panel"></div>
  <div class="hero-caption">
    <div class="hero-dots"><span style="top:19px"></span><span style="top:31px"></span><span class="on" style="top:43px"></span><span style="top:55px"></span></div>
    <h2>LOREM IPSUM DOLOR SIT AMET, CONSEC<br>TETUER ADIPSCING ELIT</h2>
  </div>
</section>

<div class="dropdown">
  <ul>
    <li>NAME</li><li>OVERVIEW</li><li>MISSION</li><li>LANGUAGES SPOKEN</li>
    <li class="current">SERVICES<span class="plus"></span></li>
    <li>CLINIC POLICIES<span class="plus"></span></li>
  </ul>
</div>
<div class="submenu"><div>TITLE</div><div>DESCRIPTION</div></div>

<h2 class="section-title" style="top:407px">WELCOME TO ORRIN CLINICS</h2>
<p class="lede" style="top:432px"><span class="dark">Lorem ipsum dolor sit amet, consectetuer adipiscing elit, sed diam nonummy nibh euismod tincidunt ut laoreet dolore magna aliquam erat volutpat.</span><br>Ut wisi enim ad minim veniam, quis nostrud exerci tation ullamcorper suscipit lobortis nisl ut aliquip ex ea commodo consequat. Duis autem vel eum iriure dolor in hendrerit in vulp<br>utate velit esse molestie consequat, vel illum dolore eu feugiat nulla facilisis at vero eros et accumsan et iusto odio dignissim.</p>

<article class="widget" style="left:70px">
  <div class="widget-box">
    <div class="row"><span>Mon – Fri</span><span>8:00 – 18:00</span></div>
    <div class="row"><span>Saturday</span><span>9:00 – 13:00</span></div>
    <div class="row"><span>Sunday</span><span>Closed</span></div>
    <div class="row"><span>Holidays</span><span>Closed</span></div>
  </div>
  <h3>Hours of Operation</h3>
  <p>Walk-ins are welcome during open hours. Please call ahead for booked visits.</p>
</article>
<article class="widget" style="left:227px">
  <div class="widget-box">
    <span class="alert">ALERT</span><br>
    Accepting New Patients<br>
    Register at the front desk or by phone.<br>
    <a>Read bulletins</a>
  </div>
  <h3>Bulletins</h3>
  <p>Ut tellus dolor, dapibus eget, elementum vel, cursus eleifend, elit. Lorem ipsum dolor sit amet.</p>
</article>
<article class="widget" style="left:385px">
  <div class="widget-box">
    1. Late Arrivals<br>
    2. Missed Appointments<br>
    3. Fees<br>
    <a>View all clinic policies</a>
  </div>
  <h3>Clinic Policies</h3>
  <p>Ut tellus dolor, dapibus eget, elementum vel, cursus eleifend, elit. Lorem ipsum dolor sit amet.</p>
</article>
<article class="widget" style="left:542px">
  <div class="widget-box">
    Tel: (555) 014 229 000<br>
    Fax: (555) 014 229 000<br>
    hello@orrinclinics.com<br>
    48 Alder Row, Kestfield<br>
    <a>Get directions</a>
  </div>
  <h3>Contact Info</h3>
  <p>Ut tellus dolor, dapibus eget, elementum vel, cursus eleifend, elit. Lorem ipsum dolor sit amet.</p>
</article>

<section class="band" style="top:664px;height:130px"></section>
<h2 class="section-title" style="top:682px">PHYSICIAN TOOLBOX</h2>
<p class="lede" style="top:705px">Duis autem vel eum iriure dolor in hendrerit in vulputate velit esse molestie consequat, vel illum dolore eu feugiat nulla facilisis at vero eros et accumsan et iusto odio dignissim qui<br>blandit praesent luptatum zzril delenit augue duis dolore te feugait nulla facilisi.</p>
<a class="btn-blue" style="left:345px;top:746px;width:64px;height:27px">READ MORE</a>

<h2 class="section-title" style="top:812px">OUR STAFFS</h2>
<p class="lede" style="top:836px">Lorem ipsum dolor sit amet, consectetuer adipiscing elit, sed diam nonummy nibh euismod tincidunt ut laoreet dolore magna aliquam erat volutpat.</p>

<div class="staff" style="left:71px"><h4>HARLAN VOSS</h4><div class="role">Family Physician</div><p>“ Ut wisi enim ad minim veniam, quis nostrud exerci tation ullamcorper suscipit lobortis nisl ut aliquip ex ea commodo consequat.</p></div>
<div class="staff" style="left:282px"><h4>MIRA OKAFOR</h4><div class="role">Nurse Practitioner</div><p>“ Lorem ipsum dolor sit amet, consectetuer adipiscing elit, sed diam nonummy nibh euismod tincidunt ut laoreet dolore magna aliquam erat volutpat.</p></div>
<div class="staff" style="left:491px"><h4>DANE PRESCOTT</h4><div class="role">General Practitioner</div><p>“ Duis autem vel eum iriure dolor in hendrerit in vulputate velit esse molestie consequat, vel illum dolore eu feugiat nulla facilisis at vero eros et accumsan et iusto.</p></div>

<section class="band" style="top:1010px;height:106px"></section>
<p class="cta-text">Claritas est etiam processus dynamicus, qui sequitur mutationem consuetudium lectorum. Mirum est notare quam littera gothica, quam nunc putamus parum claram, anteposuerit litterarum formas humanitatis per seacula quarta decima.</p>
<a class="btn-blue" style="left:308px;top:1070px;width:138px;height:28px"><svg width="7" height="7" viewBox="0 0 7 7"><rect x=".5" y="1.2" width="6" height="5.3" fill="none" stroke="#fff"/><rect x=".5" y="1.2" width="6" height="1.6" fill="#fff"/></svg>MAKE AN APPOINTMENT</a>

<footer class="site-footer">
  <div class="f-contact" style="left:70px"><svg width="6" height="9" viewBox="0 0 6 9"><path d="M3 0a3 3 0 0 1 3 3c0 2-3 6-3 6S0 5 0 3a3 3 0 0 1 3-3z" fill="#1a9ad3"/><circle cx="3" cy="3" r="1" fill="#0c0c0c"/></svg>48 Alder Row, Kestfield 20417</div>
  <div class="f-contact" style="left:222px"><svg width="9" height="7" viewBox="0 0 9 7"><rect width="9" height="7" fill="#1a9ad3"/><path d="M0 0l4.5 3.5L9 0" fill="none" stroke="#0c0c0c"/></svg>hello@orrinclinics.com</div>
  <div class="f-contact" style="left:336px"><svg width="8" height="8" viewBox="0 0 8 8"><rect width="8" height="8" rx="1" fill="#1a9ad3"/><path d="M2.2 1.8c0 2.4 1.6 4 4 4l.3-1-1.2-.6-.5.5c-.8-.4-1.3-.9-1.7-1.7l.5-.5-.6-1.2z" fill="#0c0c0c"/></svg>(555) 014 229 000</div>
  <div class="f-contact" style="left:430px"><svg width="9" height="8" viewBox="0 0 9 8"><rect x="2" width="5" height="3" fill="#1a9ad3"/><rect y="3" width="9" height="5" fill="#1a9ad3"/><rect x="5.5" y="4.5" width="2" height="1" fill="#0c0c0c"/></svg>(555) 014 229 000</div>
  <div class="f-rule"></div>
  <div class="f-links">Privacy Policy &nbsp;|&nbsp; Resources &nbsp;|&nbsp; Site Map</div>
  <div class="f-copy">© 2011 Orrin Clinics. All rights reserved internationally.</div>
</footer>

</body>
</html>
```